@CLLovedale Meaddow Company

Honey Jar label. Would like it to be square (diamond shape). Will need a space for my city and state. will need a space for my phone number. Will need to have "Grade A" on the label and "product of USA" "Honey" must be larger then any other word. Black background. Label needs to look old fashion (cir 1880s) Sketch of Mt #2Raainier attached that I have the rights to use.

Like the look of this https://shop.pellowbrint.com/pbshop/item.php?nodeid=16

Same label will also be used for a run of a limited supply of honey. So I will need one that also has "Pipkin's private batch". Pipkin is my daughter"s rabbit

```html
<!DOCTYPE html>
<html lang="en">
<head>
<meta charset="utf-8">
<title>Clovedale Meadow Co. — Honey Jar Labels</title>
<link rel="stylesheet" href="https://fonts.googleapis.com/css2?family=Oranienbaum&family=Pinyon+Script&family=Montserrat:wght@500&family=Cinzel:wght@700&display=swap">
<style>
  :root {
    --backdrop-top: #ddcb8b;
    --backdrop-bottom: #cf9630;
    --label-black: #000000;
    --label-gold: #b9961f;
    --label-red: #a3181a;
    --ribbon-red: #9c1712;
    --scene-sky: #d9d7a8;
    --scene-rock: #7a3a3c;
    --scene-meadow: #7f8a2c;
  }
  html, body {
    margin: 0;
    padding: 0;
    width: 1200px;
    height: 901px;
    overflow: hidden;
  }
  .canvas {
    position: relative;
    width: 1200px;
    height: 901px;
    background: linear-gradient(180deg, var(--backdrop-top) 0%, var(--backdrop-bottom) 58%, var(--backdrop-bottom) 100%);
  }
  .label-sheet { position: absolute; inset: 0; }
  .label-body { fill: var(--label-black); }
  .rule { stroke: var(--label-red); stroke-width: 1.2; fill: none; }
  .flourish { fill: var(--label-red); opacity: 0.55; }
  .company-name {
    font-family: "Oranienbaum", serif;
    font-size: 30px;
    fill: var(--label-gold);
    letter-spacing: 0.5px;
  }
  .script-word {
    font-family: "Pinyon Script", cursive;
    font-size: 24px;
    fill: var(--label-gold);
  }
  .condensed-word {
    font-family: "Oranienbaum", serif;
    fill: var(--label-gold);
  }
  .contact-line {
    font-family: "Montserrat", sans-serif;
    font-weight: 500;
    font-size: 12.5px;
    fill: var(--label-red);
    letter-spacing: 1.2px;
  }
  .ribbon { fill: var(--ribbon-red); }
  .ribbon-text {
    font-family: "Cinzel", serif;
    font-weight: 700;
    font-size: 15px;
    fill: var(--label-gold);
    letter-spacing: 0.6px;
  }
</style>
</head>
<body>
<main class="canvas">
  <svg class="label-sheet" width="1200" height="901" viewBox="0 0 1200 901" xmlns="http://www.w3.org/2000/svg">
    <defs>
      <linearGradient id="mountain-tones" x1="0" y1="0" x2="0" y2="1">
        <stop offset="0" stop-color="var(--scene-sky)"/>
        <stop offset="0.45" stop-color="#e8a05a"/>
        <stop offset="0.62" stop-color="var(--scene-rock)"/>
        <stop offset="1" stop-color="var(--scene-meadow)"/>
      </linearGradient>
      <path id="name-arc" d="M196 338 Q306 296 416 338"/>

      <g id="honey-label">
        <polygon class="label-body" points="14,450 306,158 598,450 306,742"/>

        <ellipse class="flourish" cx="306" cy="222" rx="60" ry="26" role="img" aria-label="Red calligraphic flourish ornament"/>
        <ellipse class="flourish" cx="306" cy="668" rx="60" ry="26" role="img" aria-label="Red calligraphic flourish ornament"/>

        <line class="rule" x1="218" y1="264" x2="394" y2="264"/>
        <line class="rule" x1="210" y1="271" x2="402" y2="271"/>
        <line class="rule" x1="202" y1="278" x2="410" y2="278"/>
        <line class="rule" x1="186" y1="296" x2="66" y2="416"/>
        <line class="rule" x1="426" y1="296" x2="546" y2="416"/>
        <line class="rule" x1="202" y1="612" x2="410" y2="612"/>
        <line class="rule" x1="210" y1="619" x2="402" y2="619"/>
        <line class="rule" x1="218" y1="626" x2="394" y2="626"/>

        <text class="company-name" text-anchor="middle">
          <textPath href="#name-arc" startOffset="50%" textLength="210" lengthAdjust="spacingAndGlyphs">CLOVEDALE MEADOW CO.</textPath>
        </text>

        <ellipse cx="306" cy="392" rx="126" ry="57" fill="url(#mountain-tones)" role="img" aria-label="Vintage engraved sketch of a snow-capped mountain above a meadow"/>

        <text class="script-word" x="108" y="436" text-anchor="middle">Product of</text>
        <text class="condensed-word" x="107" y="476" font-size="40" text-anchor="middle" textLength="50" lengthAdjust="spacingAndGlyphs">USA</text>
        <text class="script-word" x="498" y="440" text-anchor="middle">Grade</text>
        <text class="condensed-word" x="498" y="482" font-size="40" text-anchor="middle">A</text>

        <text class="contact-line" transform="translate(82 496) rotate(45)">TEL. 1-800-MEADOWS</text>
        <text class="contact-line" transform="translate(428 603) rotate(-45)" textLength="176" lengthAdjust="spacingAndGlyphs">ALDERBROOK, WASHINGTON</text>

        <text class="condensed-word" x="306" y="600" font-size="116" text-anchor="middle" textLength="206" lengthAdjust="spacingAndGlyphs">HONEY</text>
      </g>
    </defs>

    <use href="#honey-label"/>

    <g transform="translate(588 0)">
      <use href="#honey-label"/>
      <path class="ribbon" d="M180 484 Q306 470 432 484 L430 514 Q306 500 182 514 Z"/>
      <text class="ribbon-text" x="306" y="500" text-anchor="middle" textLength="236" lengthAdjust="spacingAndGlyphs">PIPKIN'S PRIVATE BATCH</text>
    </g>
  </svg>
</main>
</body>
</html>
```